MirelaStyle e-commerce website design for shopify platform

I currently have a trendy e-commerce clothing store that is primarily based off of the Southern California Style/Trends. I am looking for a redesign of my shopify template as I don't like my current image. I am looking for a sleek clean design that allows more focus on the products. I like neutral backgrounds and easy to use websites. Should be responsive to mobile devices. I would also like to have some ideas for a slide show picture that notifies customers of free shipping if possible. I do also have a theme template that I purchased through Shopify so one could set the theme up for me and edit it to what I need. My website is mirelastyle.com if you would like to look at the type of products I have. I am also looking to do a logo redesign as well- looking for a more stylish logo that would appeal to an approximate age range of 18-40 year old women. I want to be remembered, something to match the web design.

I like teal/turquoise and grey combos but I don't have to have this as the colors.

Target Market(s)

approx. 18-40

Industry/Entity Type

E-Commerce

Number of Pages Required

2 page

Requirements
Must have
• Menu bar, shopify compatible, easy to access/navigate, responsive to mobile devices, easy product upload
Nice to have
• if able ability to resize pictures all to the same size
Should not have
• not be difficult to navigate both on a reg. computer or mobile device

```html
<!DOCTYPE html>
<html lang="en">
<head>
<meta charset="utf-8">
<title>MirelaStyle – Home</title>
<link href="https://fonts.googleapis.com/css2?family=Arimo:wght@400;700&family=Open+Sans:wght@300;400;600&display=swap" rel="stylesheet">
<style>
:root{
  --teal:#1f93a8;
  --teal-dark:#17707f;
  --head:#20889b;
  --nav:#196c7b;
  --page:#ececec;
  --card:#ffffff;
  --ink:#333333;
  --muted:#8a8a8a;
  --red:#d9472f;
  --mustard:#c9a21a;
  --purple:#8a2f9c;
  --green:#3d9a3d;
  --charcoal:#3a3a3a;
  --foot:#1a5663;
  --foot-bar:#ececec;
  --overlay:rgba(0,0,0,.68);
}
*{box-sizing:border-box;margin:0;padding:0}
html,body{width:1110px;height:1200px;overflow:hidden;background:var(--page)}
body{font-family:"Arimo",Arial,sans-serif;color:var(--ink)}
.page{position:relative;width:1200px;height:1297px;transform:scale(.925);transform-origin:0 0;background:var(--page)}
.abs{position:absolute}
/* header */
.topbar{left:0;top:0;width:1200px;height:40px;background:var(--head)}
.brand{left:240px;top:11px;font:700 14px/18px "Arimo",Arial,sans-serif;color:#fff;display:flex;align-items:center;gap:5px;white-space:nowrap}
.brand i{display:block;width:8px;height:8px;border-radius:50%;background:#fff}
.search{left:348px;top:9px;width:341px;height:21px;display:flex}
.search span{flex:1;background:#fff;font-size:10px;color:#aaa;padding:5px 8px;white-space:nowrap;overflow:hidden}
.search b{width:61px;background:var(--mustard);color:#fff;font-size:10px;text-align:center;line-height:21px}
.account{right:240px;top:14px;font-size:10px;color:#fff}
.navbar{left:0;top:40px;width:1200px;height:33px;background:var(--nav);padding-left:249px;display:flex;gap:19px;align-items:center}
.navbar a{font-size:9.5px;color:#fff;text-decoration:none;letter-spacing:.2px}
/* hero */
.hero{left:240px;top:92px;width:535px;height:221px;background:linear-gradient(90deg,#6e6a63,#b9b1a6 45%,#3b3633)}
.sale{left:282px;top:126px;width:168px;height:159px;background:var(--mustard);text-align:center;color:#fff}
.sale h2{font:700 32px Georgia,serif;margin-top:6px;letter-spacing:1px}
.sale .pct{background:#23566a;font:300 21px "Open Sans",sans-serif;padding:5px 0;margin-top:6px}
.sale p{font-size:10px;margin:12px 14px 0;line-height:14px}
.sale .cart{display:inline-block;background:var(--teal);font-size:9px;font-weight:700;padding:6px 8px;margin-top:8px}
.arrow{top:184px;width:28px;height:38px;background:rgba(0,0,0,.45)}
/* side panel */
.promo{left:795px;top:92px;width:165px;height:221px;background:#fff}
.promo .free{background:var(--purple);color:#fff;padding:8px 8px;height:42px;white-space:nowrap}
.promo .free b,.promo .free em{font-size:10.5px;font-style:normal}
.promo .free small{display:block;font-size:8.5px;margin-top:3px}
.promo .get{font-size:9px;padding:9px 8px 5px;white-space:nowrap}
.promo .field{margin:0 12px;border:1px solid #ddd;height:20px;font-size:8.5px;color:#aaa;padding:5px 8px}
.promo .sign{display:inline-block;margin:7px 12px;background:var(--teal);color:#fff;font-size:9px;font-weight:700;padding:5px 9px}
.store{width:165px;height:49px}
/* sections */
.heading{left:240px;width:720px;font:300 19px "Open Sans",sans-serif;color:var(--red);border-bottom:3px solid var(--red);padding-bottom:3px}
.cat{width:233px;height:47px;background:var(--card);padding:9px 0 0 45px}
.cat .ic{position:absolute;left:15px;top:15px;width:16px;height:17px;border-radius:3px}
.cat h3{font-weight:400;font-size:14px}
.cat p{font-size:8.5px;color:#aaa;margin-top:3px;white-space:nowrap}
.product{width:173px;height:209px;background:var(--card);padding:6px}
.product .photo{height:88px}
.product .strip{height:20px;background:var(--mustard);color:#fff;font-size:9.5px;display:flex;justify-content:space-between;align-items:center;padding:0 6px}
.product h4{font-weight:400;font-size:11.5px;margin-top:6px;white-space:nowrap}
.product p{font-size:7.5px;color:#999;line-height:11.5px;margin-top:4px;height:36px}
.product .meta{display:flex;justify-content:space-between;align-items:center;margin-top:15px}
.product .meta span{font-size:7.5px;color:#aaa}
.product .btn{background:var(--teal);color:#fff;font-size:10px;font-weight:700;padding:6px 9px}
.more{left:546px;top:1024px;width:108px;height:31px;border:2px solid var(--teal);color:var(--teal);font-size:9px;font-weight:700;text-align:center;line-height:27px}
/* footer */
.footer{left:0;top:1073px;width:1200px;height:188px;background:var(--foot)}
.col{top:1092px;width:120px}
.col h5{font-size:9px;font-weight:700;color:#fff;margin-bottom:13px;white-space:nowrap}
.col li{list-style:none;font-size:9px;color:#cfe3e7;margin-bottom:13px;white-space:nowrap}
.col li:before{content:"› ";}
.quote{left:742px;top:1112px;width:218px;border-left:1px solid rgba(255,255,255,.25);height:120px}
.avatar{left:818px;top:1092px;width:60px;height:60px;border-radius:50%;background:radial-gradient(#c08a6e,#6b3b2a);border:3px solid #fff}
.quote-text{left:772px;top:1159px;width:188px;font:italic 10px/14px "Open Sans",sans-serif;color:#e0eef1}
.who{right:240px;top:1217px;text-align:right;font-size:9.5px;color:#fff;font-weight:700;line-height:14px}
.who span{font-weight:400;display:block}
.bottom{left:0;top:1261px;width:1200px;height:36px;background:var(--foot-bar)}
.links{left:240px;top:1274px;font-size:8px;color:#444;white-space:nowrap}
.pay{left:662px;top:1272px;display:flex;gap:4px}
.pay i{display:block;width:20px;height:13px;background:#6a86a8}
.social{left:783px;top:1273px;display:flex;gap:8px}
.social i{display:block;width:13px;height:13px;border-radius:50%;background:#777}
/* overlay + modal */
.overlay{left:0;top:0;width:1200px;height:1297px;background:var(--overlay)}
.modal{left:425px;top:223px;width:350px;height:202px;background:#f3f3f3}
.modal header{background:var(--teal);height:48px;padding:9px 12px;color:#fff}
.modal header h2{font:400 14px "Open Sans",sans-serif;white-space:nowrap}
.modal header p{font-size:8.5px;color:#d2f2f7;margin-top:2px}
.modal .input{margin:14px 12px 0;height:26px;background:#fff;border:1px solid #dcdcdc;font:400 9px "Open Sans",sans-serif;color:#999;padding:7px 9px}
.modal .input+.input{margin-top:5px}
.modal label{display:flex;gap:3px;align-items:center;font-size:8px;margin:7px 13px}
.modal .sub{display:block;margin:7px auto 0;width:109px;background:var(--teal);color:#fff;font-size:9.5px;font-weight:700;text-align:center;line-height:21px}
.modal footer{position:absolute;left:0;bottom:0;width:350px;height:20px;background:#ddd;font-size:7.5px;color:#555;padding:5px 12px}
.close{left:765px;top:213px;width:21px;height:21px}
</style>
</head>
<body>
<div class="page">
  <div class="abs topbar"></div>
  <div class="abs brand"><i></i>MirelaStyle</div>
  <div class="abs search"><span>Search for a product, category or brand</span><b>SEARCH</b></div>
  <div class="abs account">Log in | Sign up | Dutch ▾</div>
  <nav class="abs navbar"><a>▦ CATEGORIES ▾</a><a>WHAT'S NEW</a><a>SALE</a><a>ABOUT US</a><a>CONTACT US</a></nav>

  <div class="abs hero" role="img" aria-label="Fashion photo of a couple in winter clothing in a boutique"></div>
  <div class="abs sale"><h2>SALE</h2><div class="pct">Up to 50% off</div><p>THIS OFFER IS VALID ON ALL XYZ BRANDS.</p><span class="cart">ADD TO CART ›</span></div>
  <div class="abs arrow" style="left:240px"><svg width="28" height="38"><path d="M17 13l-6 6 6 6" stroke="#fff" stroke-width="2" fill="none"/></svg></div>
  <div class="abs arrow" style="left:747px"><svg width="28" height="38"><path d="M11 13l6 6-6 6" stroke="#fff" stroke-width="2" fill="none"/></svg></div>

  <aside class="abs promo">
    <div class="free"><b>Free</b> <em>Discount on MirelaStyle</em><small>● Find items ● use it ● Enjoy it</small></div>
    <div class="get">Get MirelaStyle Clothing by Email</div>
    <div class="field">Enter your email here</div>
    <span class="sign">SIGN UP NOW ›</span>
    <div class="store" style="background:var(--green);margin-top:4px"></div>
    <div class="store" style="background:var(--charcoal)"></div>
  </aside>

  <h2 class="abs heading" style="top:326px">Popular Categories</h2>
  <div class="abs cat" style="left:240px;top:366px"><span class="ic" style="background:#e08a2a"></span><h3>Deals &amp; Offers</h3><p>Top Deals &amp; offers across 100+ Stores</p></div>
  <div class="abs cat" style="left:484px;top:366px"><span class="ic" style="background:#2a8fc4"></span><h3>New Arrivals</h3><p>Top Deals &amp; offers across 100+ Stores</p></div>
  <div class="abs cat" style="left:728px;top:366px"><span class="ic" style="background:#9a5bb0"></span><h3>Fashion Accessories</h3><p>Top Deals &amp; offers across 100+ Stores</p></div>
  <div class="abs cat" style="left:240px;top:423px"><span class="ic" style="background:#d9475f"></span><h3>Tops</h3><p>Top Deals &amp; offers across 100+ Stores</p></div>
  <div class="abs cat" style="left:484px;top:423px"><span class="ic" style="background:#234f8a"></span><h3>Shoes Accessories</h3><p>Top Deals &amp; offers across 100+ Stores</p></div>
  <div class="abs cat" style="left:728px;top:423px"><span class="ic" style="background:#c23d8f"></span><h3>Dresses</h3><p>Top Deals &amp; offers across 100+ Stores</p></div>
  <div class="abs cat" style="left:240px;top:481px"><span class="ic" style="background:#1f5aa8"></span><h3>Bottoms / Rompers</h3><p>Top Deals &amp; offers across 100+ Stores</p></div>
  <div class="abs cat" style="left:484px;top:481px"><span class="ic" style="background:#2e9a7a"></span><h3>Ethnic Wear</h3><p>Top Deals &amp; offers across 100+ Stores</p></div>
  <div class="abs cat" style="left:728px;top:481px"><span class="ic" style="background:#8a5a2a"></span><h3>Personal Care</h3><p>Top Deals &amp; offers across 100+ Stores</p></div>

  <h2 class="abs heading" style="top:543px">What's New!</h2>

  <div class="abs product" style="left:240px;top:580px"><div class="photo" role="img" aria-label="Three women in striped knit cardigans" style="background:linear-gradient(90deg,#5b4a52,#d9d2cc,#4a4450)"></div><div class="strip">Upto 50% off<span>★★★★☆</span></div><h4>Women's Diva Items</h4><p>Get Additional 25% OFF on purchase of Rs.999 &amp; above from MirelaStyle for Men's and Women's products.</p><div class="meta"><span>⌖10 ◉215</span><span class="btn">GET IT NOW</span></div></div>
  <div class="abs product" style="left:421px;top:580px"><div class="photo" role="img" aria-label="Couple in dark leather jackets" style="background:linear-gradient(90deg,#3a3838,#777270,#2a2828)"></div><div class="strip">Upto 10% off<span>★★★★★</span></div><h4>Brand New Focus</h4><p>Get Additional 25% OFF on purchase of Rs.999 &amp; above from MirelaStyle for Men's and Women's products.</p><div class="meta"><span>⌖10 ◉215</span><span class="btn">GET IT NOW</span></div></div>
  <div class="abs product" style="left:604px;top:580px"><div class="photo" role="img" aria-label="Woman in a colourful printed sari" style="background:linear-gradient(90deg,#6a2a2a,#b84a3a,#3a5a4a)"></div><div class="strip">Upto 25% off<span>★★★★☆</span></div><h4>Discover Today</h4><p>Get Additional 25% OFF on purchase of Rs.999 &amp; above from MirelaStyle for Men's and Women's products.</p><div class="meta"><span>⌖10 ◉215</span><span class="btn">GET IT NOW</span></div></div>
  <div class="abs product" style="left:787px;top:580px"><div class="photo" role="img" aria-label="Pairs of women's flat shoes" style="background:linear-gradient(90deg,#8a8e92,#5a2a22,#c0b8b0)"></div><div class="strip">Upto 50% off<span>★★★☆☆</span></div><h4>Footwear (Men's &amp; Women's)</h4><p>Get Additional 25% OFF on purchase of Rs.999 &amp; above from MirelaStyle for Men's and Women's products.</p><div class="meta"><span>⌖12 ◉215</span><span class="btn">GET IT NOW</span></div></div>

  <div class="abs product" style="left:240px;top:798px"><div class="photo" role="img" aria-label="Woman modelling lingerie" style="background:linear-gradient(90deg,#a89888,#e0d8cc,#6a5a4e)"></div><div class="strip">Upto 50% off<span>★★★★☆</span></div><h4>Dream Outfit</h4><p>Get Additional 25% OFF on purchase of Rs.999 &amp; above from MirelaStyle for Men's and Women's products.</p><div class="meta"><span>⌖10 ◉215</span><span class="btn">GET IT NOW</span></div></div>
  <div class="abs product" style="left:421px;top:798px"><div class="photo" role="img" aria-label="Three children in casual outfits" style="background:linear-gradient(90deg,#cfc7bb,#b2542c,#d8d2c8)"></div><div class="strip">Upto 50% off<span>★★★★★</span></div><h4>Baby &amp; Kids</h4><p>Get Additional 25% OFF on purchase of Rs.999 &amp; above from MirelaStyle for Men's and Women's products.</p><div class="meta"><span>⌖10 ◉215</span><span class="btn">GET IT NOW</span></div></div>
  <div class="abs product" style="left:604px;top:798px"><div class="photo" role="img" aria-label="Woman in a printed summer top" style="background:linear-gradient(90deg,#c8a88e,#a23a4a,#d8c0a8)"></div><div class="strip">Upto 25% off<span>★★★★☆</span></div><h4>Funkist Pices</h4><p>Get Additional 25% OFF on purchase of Rs.999 &amp; above from MirelaStyle for Men's and Women's products.</p><div class="meta"><span>⌖10 ◉215</span><span class="btn">GET IT NOW</span></div></div>
  <div class="abs product" style="left:787px;top:798px"><div class="photo" role="img" aria-label="Woman in a bright patterned blouse" style="background:linear-gradient(90deg,#2a4a8a,#8a3a8a,#3a5aa0)"></div><div class="strip">Upto 20% off<span>★★★☆☆</span></div><h4>Super Sundays</h4><p>Get Additional 25% OFF on purchase of Rs.999 &amp; above from MirelaStyle for Men's and Women's products.</p><div class="meta"><span>⌖10 ◉215</span><span class="btn">GET IT NOW</span></div></div>

  <div class="abs more">VIEW MORE ITEM ›</div>

  <footer class="abs footer"></footer>
  <div class="abs col" style="left:240px"><h5>QUICK LINKS</h5><ul><li>Top 20</li><li>All Shops</li><li>Categories</li><li>Privacy Policy</li><li>Terms &amp; Conditions</li><li>Help</li></ul></div>
  <div class="abs col" style="left:363px"><h5>ABOUT MIRELASTYLE</h5><ul><li>Coupons</li><li>Job Offers</li><li>Contact Us</li><li>Bank Offers</li><li>Press</li><li>About Us</li></ul></div>
  <div class="abs col" style="left:486px"><h5>PARTNERS</h5><ul><li>Tavora</li><li>Roomly</li><li>PriceKite</li><li>Deskwell</li><li>Homefable</li><li>Platebird</li></ul></div>
  <div class="abs col" style="left:609px;width:130px"><h5>INTERNATIONAL</h5><ul><li>Cartnest Coupons</li><li>Being social</li><li>Tavora Coupons</li><li>Deals</li><li>Dealvia International</li><li>Platebird</li></ul></div>
  <div class="abs quote"></div>
  <div class="abs avatar" role="img" aria-label="Customer portrait"></div>
  <p class="abs quote-text">“ Sed lacinia, nibh sit amet auctor vestibulum, enim risus condimentum erat, quis vestibulum mi.. ”</p>
  <div class="abs who">Lorena Vasse<span>USA</span></div>

  <div class="abs bottom"></div>
  <div class="abs links">Home | Categories | What's New | Sale | About us | Contact us | Photofeed | Copyright © 2014 by MirelaStyle</div>
  <div class="abs pay"><i></i><i style="background:#d98a2a"></i><i style="background:#3a5aa8"></i><i style="background:#c8402a"></i><i style="background:#5a8ac0"></i></div>
  <div class="abs social"><i></i><i></i><i></i><i></i><i></i><i></i><i></i><i></i><i></i></div>

  <div class="abs overlay"></div>
  <section class="abs modal">
    <header><h2>Subscribe to MirelaStyle clothing offers by email</h2><p>Receive new offers for MirelaStyle right in your inbox!</p></header>
    <div class="input">City or Zip Code</div>
    <div class="input">Email ID</div>
    <label><svg width="9" height="9"><rect x=".5" y=".5" width="8" height="8" fill="#fff" stroke="#555"/><path d="M2 4.5l2 2 3-4" stroke="#333" stroke-width="1.3" fill="none"/></svg>Subscribe for Newsletter</label>
    <span class="sub">SUBSCRIBE NOW !</span>
    <footer>🔒 We promise we won't share your email address with anyone</footer>
  </section>
  <svg class="abs close" viewBox="0 0 21 21"><circle cx="10.5" cy="10.5" r="9.5" fill="#e04a3a" stroke="#fff" stroke-width="1.5"/><path d="M7 7l7 7M14 7l-7 7" stroke="#fff" stroke-width="2"/></svg>
</div>
</body>
</html>
```